Dietitian needs awesome business card

I need a contemporary design that's eye catching but professional.
My card is to given to doctors, specialists and patients alike.
I manage patients with chronic diseases
I have uploaded my logo and current business card, I would also like the other Certified Clinical Nutritionist logo incorporated into the design

Target Market(s)

Doctors, specialists and patients

Industry/Entity Type

Healthcare

Contact Information for Business Card

www.brightfieldnutrition.com.au
Ph: 0427 561 903
Fax: 6457 2183
email: marcus.k.diet@fernmail.com
Space on the back of the card with: Appointment date, Appointment time and appointment location

Font styles to use
Serif

Colors
fbee3e
876aae
ffc214

Requirements
Must have
• My Logo
• Certified Clinical Nutritionist Logo
• My 4 locations - Pinebrook Medical Centre, North Corrin Health, Hollis Medical, Ashcombe Doctors Surgery
Nice to have
• I like the colours in my current business card

```html
<!DOCTYPE html>
<html lang="en">
<head>
<meta charset="utf-8">
<title>Brightfield Nutrition &amp; Dietetics – Business Card</title>
<link rel="stylesheet" href="https://fonts.googleapis.com/css2?family=Tinos:wght@400;700&family=Arimo:wght@400;700&display=swap">
<style>
  :root {
    --bg: #e9eaec;
    --paper: #ffffff;
    --navy: #1f3f95;
    --leaf: #8cc63f;
    --leaf-deep: #5fae2e;
    --leaf-light: #c4e25a;
    --orange: #f47b20;
    --orange-light: #f9a66a;
    --rule: #b9bcc4;
    --ink: #4a4d57;
    --white: #ffffff;
  }
  * { box-sizing: border-box; margin: 0; padding: 0; }
  html, body { width: 1200px; height: 950px; overflow: hidden; background: var(--bg); }
  .canvas { position: relative; width: 1200px; height: 950px; }

  .card {
    position: absolute; width: 760px; height: 434px;
    background: var(--paper); overflow: hidden;
    box-shadow: 0 6px 20px rgba(0,0,0,.18);
  }
  .card--back { left: 110px; top: 36px; }
  .card--front { left: 330px; top: 486px; }

  /* brand lockup */
  .brand { position: absolute; display: flex; align-items: center; gap: 12px; }
  .brand__dot { border-radius: 50%; background: var(--navy); flex: none; }
  .brand__name {
    font-family: "Tinos", serif; font-weight: 400; color: var(--navy); line-height: 1;
  }
  .brand__name span { display: block; }
  .card--back .brand { left: 40px; top: 120px; }
  .card--back .brand__dot { width: 44px; height: 44px; }
  .card--back .brand__name { font-size: 34px; }
  .card--back .brand__name .brand__sub { font-size: 17px; margin-top: 4px; }

  /* credential badge */
  .badge {
    position: absolute; right: 40px; top: 26px; width: 170px; height: 68px;
    background: var(--orange); display: flex; align-items: center; gap: 10px; padding: 0 12px;
  }
  .badge__label {
    font-family: "Arimo", sans-serif; font-size: 11px; line-height: 1.25; color: var(--white); flex: 1;
  }
  .badge__mark { width: 48px; height: 48px; background: var(--orange-light); flex: none; }

  /* appointment form */
  .form { position: absolute; inset: 0; font-family: "Arimo", sans-serif; color: var(--ink); }
  .rule { position: absolute; height: 1px; background: var(--rule); }
  .field-label { position: absolute; font-size: 16px; color: var(--navy); }
  .ampm { position: absolute; font-size: 12px; color: var(--navy); }
  .location {
    position: absolute; display: flex; align-items: center; gap: 8px; font-size: 16px; color: var(--ink);
  }
  .location::before {
    content: ""; width: 13px; height: 13px; border: 1.5px solid var(--navy); flex: none;
  }

  /* front */
  .front-art { position: absolute; inset: 0; }
  .card--front .brand { left: 50px; top: 140px; }
  .card--front .brand__dot { width: 56px; height: 56px; }
  .card--front .brand__name { font-size: 44px; }
  .card--front .brand__name .brand__sub { font-size: 21px; margin-top: 4px; }
  .person { position: absolute; left: 210px; top: 245px; font-family: "Arimo", sans-serif; }
  .person__name { font-size: 22px; font-weight: 700; color: var(--navy); }
  .person__role { font-size: 16px; font-weight: 700; color: var(--leaf-deep); margin-top: 6px; }
  .contact {
    position: absolute; right: 26px; top: 160px; list-style: none;
    font-family: "Arimo", sans-serif; font-size: 15px; color: var(--white); text-align: right;
  }
  .contact li { display: flex; justify-content: flex-end; align-items: center; gap: 8px; height: 24px; }
  .contact svg { width: 15px; height: 15px; flex: none; }
  .contact .gap { height: 26px; }
</style>
</head>
<body>
<main class="canvas">

  <section class="card card--back" aria-label="Card back – appointment">
    <div class="brand">
      <span class="brand__dot"></span>
      <div class="brand__name"><span>Brightfield</span><span class="brand__sub">Nutrition &amp; Dietetics</span></div>
    </div>

    <div class="badge">
      <span class="badge__label">Certified Clinical Nutritionist</span>
      <span class="badge__mark"></span>
    </div>

    <div class="form">
      <div class="rule" style="left:330px; top:120px; width:390px;"></div>
      <div class="rule" style="left:330px; top:160px; width:390px;"></div>
      <div class="ampm" style="left:690px; top:130px;">AM/PM</div>

      <div class="field-label" style="left:440px; top:176px;">Time :</div>
      <div class="rule" style="left:500px; top:194px; width:220px;"></div>

      <div class="rule" style="left:40px; top:200px; width:300px;"></div>
      <div class="rule" style="left:40px; top:245px; width:300px;"></div>

      <div class="location" style="left:440px; top:214px;">Ashcombe Doctors Surgery</div>
      <div class="location" style="left:440px; top:240px;">Hollis Medical</div>

      <div class="field-label" style="left:40px; top:290px;">Date :</div>
      <div class="rule" style="left:100px; top:308px; width:300px;"></div>

      <div class="location" style="left:40px; top:336px;">Pinebrook Medical Centre</div>
      <div class="location" style="left:40px; top:362px;">North Corrin Health</div>
    </div>
  </section>

  <section class="card card--front" aria-label="Card front">
    <svg class="front-art" viewBox="0 0 760 434" preserveAspectRatio="none" aria-hidden="true">
      <defs>
        <linearGradient id="leafFill" x1="0" y1="0" x2="1" y2="1">
          <stop offset="0" stop-color="var(--leaf-light)"/>
          <stop offset="0.6" stop-color="var(--leaf)"/>
          <stop offset="1" stop-color="var(--leaf-deep)"/>
        </linearGradient>
      </defs>
      <path d="M540 0 L760 0 L760 434 L0 434 L0 388 C240 410 500 330 540 0 Z" fill="url(#leafFill)"/>
      <path d="M580 0 C560 300 320 390 20 405" fill="none" stroke="var(--white)" stroke-width="5"/>
    </svg>

    <div class="brand">
      <span class="brand__dot"></span>
      <div class="brand__name"><span>Brightfield</span><span class="brand__sub">Nutrition &amp; Dietetics</span></div>
    </div>

    <div class="person">
      <div class="person__name">Marcus Kellerman</div>
      <div class="person__role">Nutritionist &amp; Chef</div>
    </div>

    <ul class="contact">
      <li>0427 561 903
        <svg viewBox="0 0 16 16"><path fill="#fff" d="M3 1l3 3-1.5 2c1 2 3 4 5 5L11.5 9.5l3 3-2 2.5C6 14 2 10 1 3z"/></svg></li>
      <li>6457 2183
        <svg viewBox="0 0 16 16"><rect x="2" y="6" width="12" height="8" fill="#fff"/><rect x="4" y="1" width="8" height="5" fill="none" stroke="#fff" stroke-width="1.5"/></svg></li>
      <li class="gap"></li>
      <li>marcus.k.diet@fernmail.com
        <svg viewBox="0 0 16 16"><rect x="1" y="3" width="14" height="10" fill="#fff"/><path d="M1 3l7 6 7-6" fill="none" stroke="var(--leaf)" stroke-width="1.3"/></svg></li>
      <li>www.brightfieldnutrition.com.au
        <svg viewBox="0 0 16 16"><circle cx="8" cy="8" r="6.5" fill="none" stroke="#fff" stroke-width="1.5"/><path d="M1.5 8h13M8 1.5c-3 3-3 10 0 13M8 1.5c3 3 3 10 0 13" fill="none" stroke="#fff" stroke-width="1.2"/></svg></li>
    </ul>
  </section>

</main>
</body>
</html>
```